New Company Business Card design

Looking for a corporate looking business card utilising my new logo design - the logo i would like embossed as one option and flat as another - simplistic but stylish - less is more - we are an import export business launching into the market - i would like a couple of options as main background - Grey or Black

```html
<!DOCTYPE html>
<html lang="en">
<head>
<meta charset="utf-8">
<title>Northgate Trade Partners — Business Card</title>
<link href="https://fonts.googleapis.com/css2?family=Roboto:wght@400;500&display=swap" rel="stylesheet">
<style>
  :root {
    --canvas-bg: #e9e7e3;
    --card-white: #f3f3f3;
    --brand-blue: #1173bd;
    --rule-grey: #6d6e70;
    --tagline-grey: #6d6e70;
    --card-black: #1b1c1d;
    --text-white: #ffffff;
  }
  * { margin: 0; padding: 0; box-sizing: border-box; }
  html, body { width: 1200px; height: 960px; overflow: hidden; }
  body {
    background: var(--canvas-bg);
    font-family: "Roboto", Arial, sans-serif;
    position: relative;
  }
  .card {
    position: absolute;
    width: 600px;
    height: 343px;
    box-shadow: 0 4px 10px rgba(0,0,0,0.25);
    overflow: hidden;
  }
  .card-front { left: 314px; top: 113px; background: var(--card-white); }
  .card-back { left: 311px; top: 473px; background: var(--card-black); }

  .front-band { position: absolute; left: 0; top: 0; width: 600px; height: 343px; }

  .brand-block {
    position: absolute;
    left: 0; top: 66px; width: 600px;
    text-align: center;
  }
  .brand-name {
    display: inline-flex;
    align-items: center;
    gap: 10px;
    color: var(--brand-blue);
    font-weight: 500;
    font-size: 27px;
    letter-spacing: 0.5px;
    text-transform: uppercase;
  }
  .brand-dot {
    width: 18px; height: 18px;
    border-radius: 50%;
    background: var(--brand-blue);
  }
  .tagline {
    margin-top: 8px;
    color: var(--tagline-grey);
    font-size: 9px;
    letter-spacing: 2px;
    text-transform: uppercase;
  }

  .person {
    position: absolute;
    left: 36px; top: 230px;
    color: var(--text-white);
  }
  .person-name { font-size: 21px; font-weight: 500; line-height: 24px; }
  .person-role { font-size: 15px; font-weight: 500; line-height: 20px; }
  .person-address { margin-top: 6px; font-size: 14px; line-height: 19px; }

  .contact-list {
    position: absolute;
    right: 36px; top: 235px;
    list-style: none;
    color: var(--text-white);
    font-size: 14px;
    line-height: 19.5px;
    text-align: right;
  }
  .contact-list li { display: flex; justify-content: flex-end; align-items: center; gap: 5px; }
  .contact-list svg { width: 13px; height: 13px; fill: var(--text-white); }

  .back-brand {
    position: absolute;
    left: 0; top: 120px; width: 600px;
    display: flex; justify-content: center; align-items: center; gap: 16px;
    color: var(--text-white);
    font-weight: 500;
    font-size: 56px;
    letter-spacing: 1px;
  }
  .back-dot {
    width: 36px; height: 36px;
    border-radius: 50%;
    background: var(--text-white);
  }
  .website {
    position: absolute;
    left: 0; top: 287px; width: 600px;
    text-align: center;
    color: var(--text-white);
    font-size: 14px;
    letter-spacing: 2.6px;
  }
</style>
</head>
<body>
  <section class="card card-front">
    <svg class="front-band" viewBox="0 0 600 343" aria-hidden="true">
      <path d="M0 140 Q300 230 600 138" fill="none" stroke="var(--rule-grey)" stroke-width="5"/>
      <path d="M0 148 Q300 238 600 146 L600 343 L0 343 Z" fill="var(--brand-blue)"/>
    </svg>
    <div class="brand-block">
      <div class="brand-name"><span class="brand-dot"></span>Northgate Trade Partners</div>
      <div class="tagline">Worldwide supply for every market</div>
    </div>
    <div class="person">
      <div class="person-name">DANIEL REYES</div>
      <div class="person-role">CEO/FOUNDER</div>
      <div class="person-address">2140 Harbor View Road<br>Juneau, Alaska 99801</div>
    </div>
    <ul class="contact-list">
      <li>555 210 4471
        <svg viewBox="0 0 24 24"><path d="M6.6 10.8a15 15 0 0 0 6.6 6.6l2.2-2.2c.3-.3.7-.4 1-.2 1.1.4 2.3.6 3.6.6.6 0 1 .4 1 1V20c0 .6-.4 1-1 1A17 17 0 0 1 3 4c0-.6.4-1 1-1h3.5c.6 0 1 .4 1 1 0 1.2.2 2.4.6 3.6.1.3 0 .7-.2 1z"/></svg></li>
      <li>555 318 6620
        <svg viewBox="0 0 24 24"><path d="M7 1h10a2 2 0 0 1 2 2v18a2 2 0 0 1-2 2H7a2 2 0 0 1-2-2V3a2 2 0 0 1 2-2zm0 3v14h10V4z"/></svg></li>
      <li>555 742 0935
        <svg viewBox="0 0 24 24"><path d="M6 2h12v5H6zM3 8h18a2 2 0 0 1 2 2v7h-4v5H5v-5H1v-7a2 2 0 0 1 2-2zm4 8v4h10v-4z"/></svg></li>
      <li>hello@northgate.com
        <svg viewBox="0 0 24 24"><path d="M2 5h20v14H2zm2 2v.5l8 5 8-5V7z"/></svg></li>
    </ul>
  </section>

  <section class="card card-back">
    <div class="back-brand"><span class="back-dot"></span>Northgate</div>
    <div class="website">www.northgatetradepartners.com</div>
  </section>
</body>
</html>
```